Card design for orthopaedic surgeons working as The Brightwater Joint Centre

Business cards, letterhead

Colors

Designer to choose colors to be used in the design.

Requirements
Must have
• Late addition.
• Cards letterhead must have logos of
• Crestmoor Lindell College of Surgeons
• Varenwood Bone Health Association
Nice to have
• Back of card to have space for appointment time to be added by hand and some blank space for writing incidental other notes.

```html
<!DOCTYPE html>
<html lang="en">
<head>
<meta charset="utf-8">
<title>The Brightwater Joint Centre – Business Card</title>
<link rel="stylesheet" href="https://fonts.googleapis.com/css2?family=Lato:wght@400;700&family=Raleway:wght@400&family=Roboto:wght@400&display=swap">
<style>
  :root {
    --sky: #30b0fb;
    --navy: #062f48;
    --white: #ffffff;
    --stage: #d9dadb;
    --ink: #1b2a36;
  }
  html, body {
    margin: 0;
    padding: 0;
    width: 1200px;
    height: 802px;
    overflow: hidden;
    background: var(--stage);
  }
  .stage {
    position: relative;
    width: 1200px;
    height: 802px;
  }
  .card {
    position: absolute;
    top: 274px;
    width: 545px;
    height: 325px;
    transform: scale(0.8117);
    transform-origin: top left;
    box-shadow: 0 3px 6px rgba(0,0,0,0.35);
    overflow: hidden;
  }
  .card--front { left: 136px; background: var(--sky); }
  .card--back { left: 624px; background: var(--white); }

  .wave {
    position: absolute;
    inset: 0;
    width: 545px;
    height: 325px;
  }
  .brand-name {
    position: absolute;
    font-family: "Raleway", sans-serif;
    font-weight: 400;
    white-space: nowrap;
    margin: 0;
    letter-spacing: -0.2px;
  }
  .card--front .brand-name {
    right: 32px;
    top: 60px;
    font-size: 19px;
    color: var(--white);
  }
  .card--back .brand-name {
    left: 0;
    right: 0;
    text-align: center;
    top: 162px;
    font-size: 22px;
    color: var(--navy);
  }
  .holder {
    position: absolute;
    left: 32px;
    top: 200px;
    color: var(--white);
  }
  .holder__name {
    font-family: "Roboto", sans-serif;
    font-size: 21px;
    line-height: 1;
    margin: 0;
  }
  .holder__role {
    font-family: "Lato", sans-serif;
    font-size: 15px;
    line-height: 1;
    margin: 2px 0 0 -1px;
  }
  .address {
    position: absolute;
    left: 32px;
    top: 255px;
    font-family: "Lato", sans-serif;
    font-size: 15px;
    line-height: 20px;
    color: var(--white);
    margin: 0;
  }
  .contacts {
    position: absolute;
    right: 32px;
    top: 234px;
    list-style: none;
    margin: 0;
    padding: 0;
    font-family: "Lato", sans-serif;
    font-size: 15px;
    line-height: 20px;
    color: var(--white);
    text-align: right;
  }
  .contacts li { display: flex; align-items: center; justify-content: flex-end; gap: 3px; }
  .contacts svg { width: 11px; height: 11px; }
  .web-line {
    position: absolute;
    left: 0;
    right: 0;
    top: 275px;
    text-align: center;
    font-family: "Raleway", sans-serif;
    font-size: 16px;
    color: var(--ink);
    margin: 0;
  }
  .web-line__domain { color: var(--sky); }
</style>
</head>
<body>
<main class="stage">

  <section class="card card--front" aria-label="Business card front">
    <svg class="wave" viewBox="0 0 545 325" preserveAspectRatio="none" aria-hidden="true">
      <path d="M0 190 C60 130 130 112 190 116 C270 122 340 176 420 182 C470 186 510 172 545 150 L545 325 L0 325 Z" fill="var(--white)"/>
      <path d="M0 198 C60 140 130 122 190 126 C270 132 340 186 420 190 C470 193 510 178 545 160 L545 325 L0 325 Z" fill="var(--navy)"/>
    </svg>
    <p class="brand-name">The Brightwater Joint Centre</p>
    <div class="holder">
      <p class="holder__name">Marcus Ellery</p>
      <p class="holder__role">Managing Director</p>
    </div>
    <p class="address">421, Address line<br>here, 45452,Country Name</p>
    <ul class="contacts">
      <li>044-987 654 321
        <svg viewBox="0 0 12 12" aria-hidden="true"><path d="M1 4 Q6 0 11 4 L10 5.5 L8 4.8 L8 3.8 Q6 3 4 3.8 L4 4.8 L2 5.5 Z M3 6 L9 6 L10.5 10.5 L1.5 10.5 Z" fill="var(--white)"/></svg>
      </li>
      <li>info@brightwaterjc.com
        <svg viewBox="0 0 12 12" aria-hidden="true"><rect x="0.5" y="2" width="11" height="8" fill="var(--white)"/><path d="M0.5 2 L6 6.5 L11.5 2" fill="none" stroke="var(--navy)" stroke-width="1"/></svg>
      </li>
      <li>www.brightwaterjc.com
        <svg viewBox="0 0 12 12" aria-hidden="true"><circle cx="6" cy="6" r="5.5" fill="var(--white)"/><path d="M3 3.5 Q5 5 4 7 Q6 8 7 10 M8 2 Q7.5 4 9.5 5" fill="none" stroke="var(--navy)" stroke-width="1.1"/></svg>
      </li>
    </ul>
  </section>

  <section class="card card--back" aria-label="Business card back">
    <p class="brand-name">The Brightwater Joint Centre</p>
    <p class="web-line">www.<span class="web-line__domain">brightwaterjc</span>.com</p>
  </section>

</main>
</body>
</html>
```